Advanced Therapeutic Massage Therapist

I need a business card advertising my massage services as an advanced therapeutic massage therapist. I offer advanced therapeutic massage, swedish and deep tissue. I want to create a simple, professional and feminine card. I like bright colours and creativity.

I prefer a bold and experimental approach rather than something status-quo. A card to suggest therapeutic healing through dynamic massage. Motifs, shapes or layout which suggest movement and flow.
Updates

Target Market(s)

Everybody!

Industry/Entity Type

Health And Wellness

Contact Information for Business Card

The card should include:
My name, logo, services offered and my contact details.

Sláine Dunleavy
Massage Therapist

- Swedish - Deep Tissue - Advanced Therapeutic

Phone: (+353) 87 216 4093
Email: regenerate@slainedunleavy-example.com
Website: www.slainedunlevy-example.com

Font styles to use
Serif
Sans Serif
Decorative
Script

Colors

Designer to choose colors to be used in the design.

Requirements
Must have
• An example may contain something like this, yet concise:
• "Sláine Dunleavy
• Massage Therapist
• - Swedish - Deep Tissue - Advanced Therapeutic"
Nice to have
• This sentence is optional:
• Imagery such as a logo or symbol. I have attached a file containing a logo I had produced however the name is incorrect now as it is "Sláine" not "Nelly". It could be edited to change it to Sláine.
• I have sent the file as .psd .jpg. .pdf and .png
• I like when the card conveys energy, movement, pressure points, flow etc.
• I just like the designer to follow their own style and ideas. I like bright colours but must have a lot of a base colour to offset it. I really prefer them to follow their own inspiration. That is my preference.
Should not have
• Pine trees, non-native trees to Britain and Ireland, exotic flowers or animals that are not native to Britain and Ireland.
• I don't like brown as the background colour of the card.
• The cars shouldn't look like a wedding invitation i.e too many floral type designs.

```html
<!DOCTYPE html>
<html lang="en">
<head>
<meta charset="utf-8">
<title>Sláine Dunleavy – Massage Therapist Business Card</title>
<link rel="stylesheet" href="https://fonts.googleapis.com/css2?family=Great+Vibes&family=Questrial&family=Barlow+Semi+Condensed:wght@500&display=swap">
<style>
  :root {
    --stage: #6b6b6b;
    --card: #1f1f1f;
    --card-edge: #2a2a2a;
    --ink: #f4f4f4;
    --mint: #72c4a3;
    --gold: #c9a24a;
    --gold-deep: #8a6420;
    --seal-light: #b9ddd0;
    --seal-dark: #7fb8a5;
  }
  * { margin: 0; padding: 0; box-sizing: border-box; }
  html, body { width: 1200px; height: 550px; overflow: hidden; }
  body { background: var(--stage); position: relative; }

  .card {
    position: absolute;
    top: 158px;
    width: 391px;
    height: 235px;
    overflow: hidden;
    background: radial-gradient(circle at 50% 40%, var(--card-edge), var(--card) 70%);
    color: var(--ink);
    box-shadow: 0 0 0 1px rgba(255,255,255,0.08);
  }
  .card--front { left: 195px; }
  .card--back { left: 614px; }

  .seal {
    position: absolute;
    border-radius: 50%;
    background: radial-gradient(circle, var(--seal-light) 40%, var(--seal-dark) 85%, var(--gold-deep) 100%);
  }
  .card--front .seal { left: 137px; top: 31px; width: 116px; height: 116px; }
  .card--back .seal { left: 42px; top: 57px; width: 108px; height: 108px; }

  .name {
    position: absolute;
    font-family: "Great Vibes", cursive;
    font-size: 26px;
    line-height: 1;
    white-space: nowrap;
  }
  .role {
    position: absolute;
    font-family: "Questrial", sans-serif;
    font-size: 9.5px;
    letter-spacing: 1px;
    white-space: nowrap;
  }
  .card--front .name { left: 0; right: 0; top: 151px; text-align: center; }
  .card--front .role { left: 0; right: 0; top: 175px; text-align: center; padding-left: 4px; }

  .tagline {
    position: absolute;
    left: 0; right: 0; top: 209px;
    text-align: center;
    font-family: "Barlow Semi Condensed", sans-serif;
    font-weight: 500;
    font-size: 10.5px;
    color: var(--mint);
    white-space: nowrap;
  }

  .divider {
    position: absolute;
    left: 173px; top: 52px;
    width: 1.5px; height: 118px;
    background: linear-gradient(var(--gold-deep), var(--gold), var(--gold-deep));
  }
  .card--back .name { left: 194px; top: 62px; }
  .card--back .role { left: 201px; top: 87px; }

  .contacts { position: absolute; left: 200px; top: 112px; list-style: none; }
  .contacts li {
    display: flex; align-items: center;
    height: 17px;
    font-family: "Questrial", sans-serif;
    font-size: 10.5px;
    white-space: nowrap;
  }
  .contacts svg { width: 9px; height: 9px; margin-right: 11px; fill: var(--ink); flex: none; }

  .services {
    position: absolute;
    left: 0; right: 0; top: 209px;
    text-align: center;
    font-family: "Questrial", sans-serif;
    font-size: 11px;
    color: var(--mint);
    white-space: nowrap;
  }
</style>
</head>
<body>
  <section class="card card--front">
    <div class="seal" role="img" aria-label="Circular ornamental tree emblem in gold on mint"></div>
    <p class="name">Sláine Dunleavy</p>
    <p class="role">massage therapist</p>
    <p class="tagline">Brightwell qualified, specializing in Advanced Therapeutic &amp; Deep Tissue Massage</p>
  </section>

  <section class="card card--back">
    <div class="seal" role="img" aria-label="Circular ornamental tree emblem in gold on mint"></div>
    <div class="divider"></div>
    <p class="name">Sláine Dunleavy</p>
    <p class="role">massage therapist</p>
    <ul class="contacts">
      <li>
        <svg viewBox="0 0 10 10" aria-hidden="true"><path d="M1 3.5 Q5 0.5 9 3.5 L8 5 L6.5 4.2 L6.5 3.4 Q5 3 3.5 3.4 L3.5 4.2 L2 5 Z M2.5 5.5 L7.5 5.5 L8.5 9 L1.5 9 Z"/></svg>
        (+353) 87 216 4093
      </li>
      <li>
        <svg viewBox="0 0 10 10" aria-hidden="true"><path d="M0.5 2 H9.5 V8 H0.5 Z" fill="none" stroke="#f4f4f4" stroke-width="1"/><path d="M0.5 2 L5 5.5 L9.5 2" fill="none" stroke="#f4f4f4" stroke-width="1"/></svg>
        hi@slainedunlevy-example.com
      </li>
      <li>
        <svg viewBox="0 0 10 10" aria-hidden="true"><circle cx="5" cy="5" r="4.3" fill="none" stroke="#f4f4f4" stroke-width="1"/><ellipse cx="5" cy="5" rx="1.8" ry="4.3" fill="none" stroke="#f4f4f4" stroke-width="0.8"/><path d="M0.7 5 H9.3" stroke="#f4f4f4" stroke-width="0.8"/></svg>
        www.slainedunlevy-example.com
      </li>
    </ul>
    <p class="services">Swedish - Deep Tissue - Advanced Therapeutic</p>
  </section>
</body>
</html>
```